Non fiction book cover. The book advises how to get a new job.

The book size will be 20cm high by 13cm wide and I need a front cover which can wrap around to the back. This book has a serious message, but I've tried to make it quite light to read and accessible. So I don't want a cover that is too dour or serious and not frivolous either. At the end of the project, I will need a high resolution 3D image of the book, included as part of the package.<br/>The Title of the book is:- "Past Sixty? Hunting for your final post?<br/>by Gareth Millbrook-Ashdown".<br/>I am thinking of a light yellow background, with a striking image to attract attention. The image and words should be clear and sharp.<br/>Here is the, BACK COVER wording.<br/>"This book tells you clearly and simply the steps that you need to take, to get a job, once you’re over 50.<br/>It advises you on the techniques to use to write a killer CV.<br/>It explains how to ensure that your CV attention.<br/>It shows the best way to approach your local job agency.<br/>It demonstrates the best way to use your network.<br/><br/>This book, written by someone with 30 years’ experience in the recruitment industry, gives you ALL the answers.<br/>Whether you are a top executive or someone after some local part time work, then this book is for you. <br/>With the help of this book you will secure your next position.<br/>

Target Market(s)

UK, over 50s, male and female.

Font styles to use
Serif

Colors
fbee3e

Requirements
Must have
• A clear uncluttered cover.
Should not have
• Fussy and over complicated

```html
<!DOCTYPE html>
<html lang="en">
<head>
<meta charset="utf-8">
<title>Past Sixty? Hunting for your final post? – Cover Wrap</title>
<link rel="stylesheet" href="https://fonts.googleapis.com/css2?family=Bebas+Neue&family=Montserrat:wght@800&family=EB+Garamond:ital,wght@0,400;1,600&family=Libre+Baskerville:wght@700&display=swap">
<style>
  :root {
    --page-bg: #f3f3f3;
    --cover-yellow: #fbee3e;
    --title-red: #d8344a;
    --kicker-teal: #35a98f;
    --band-teal: #44bfa9;
    --ink: #1e1e1e;
    --art-teal: #3fbfa4;
    --art-pink: #ec7079;
    --white: #ffffff;
  }
  * { margin: 0; padding: 0; box-sizing: border-box; }
  html, body {
    width: 1200px; height: 800px; overflow: hidden;
    background: var(--page-bg);
  }
  .cover-wrap {
    position: absolute; left: 100px; top: 32px;
    width: 1000px; height: 736px;
    background: var(--cover-yellow);
    display: flex;
  }
  .bottom-band {
    position: absolute; left: 0; right: 0; bottom: 0; height: 55px;
    background: var(--band-teal);
  }
  .back-cover { position: relative; width: 467px; height: 100%; }
  .spine { position: relative; width: 61px; height: 100%; }
  .front-cover { position: relative; width: 472px; height: 100%; }

  .kicker {
    font-family: "Montserrat", sans-serif; font-weight: 800;
    color: var(--kicker-teal); text-align: center; letter-spacing: 1px;
  }
  .headline {
    font-family: "Bebas Neue", sans-serif;
    color: var(--title-red); text-align: center;
  }

  /* Back cover */
  .back-title { position: absolute; top: 40px; left: 45px; width: 400px; }
  .back-title .kicker { font-size: 26px; line-height: 1; }
  .back-title .headline { font-size: 34px; line-height: 1; margin-top: 2px; }
  .blurb {
    position: absolute; top: 130px; left: 45px; width: 400px;
    font-family: "EB Garamond", serif; color: var(--ink);
  }
  .blurb-quote { font-size: 17px; margin-bottom: 6px; }
  .blurb-points { list-style: none; margin-bottom: 8px; }
  .blurb-points li {
    position: relative; padding-left: 22px;
    font-style: italic; font-weight: 600; font-size: 13px; line-height: 1.25;
    margin-bottom: 10px;
  }
  .blurb-points li::before {
    content: ""; position: absolute; left: 6px; top: 5px;
    width: 6px; height: 6px; border-radius: 50%; background: var(--ink);
  }
  .blurb p { font-size: 14px; line-height: 1.3; text-align: justify; margin-bottom: 12px; }
  .back-art {
    position: absolute; left: 48px; top: 560px; width: 200px; height: 121px;
    background: linear-gradient(160deg, var(--cover-yellow) 30%, var(--art-pink) 60%, var(--art-teal) 85%);
  }
  .barcode-space {
    position: absolute; left: 311px; top: 646px; width: 124px; height: 67px;
    background: var(--white);
  }

  /* Spine */
  .spine-text {
    position: absolute; top: 58px; left: 50%; transform: translateX(-50%);
    writing-mode: vertical-rl; white-space: nowrap;
    display: flex; align-items: center;
  }
  .spine-text .kicker { font-size: 15px; }
  .spine-text .headline { font-size: 24px; margin-top: 4px; }
  .spine-author {
    font-family: "Libre Baskerville", serif; font-weight: 700;
    font-size: 13px; color: var(--ink); margin-top: 24px;
  }

  /* Front cover */
  .front-title { position: absolute; top: 40px; left: 20px; width: 432px; }
  .front-title .kicker { font-size: 44px; line-height: 1; }
  .front-title .headline { font-size: 84px; line-height: 0.92; margin-top: 8px; }
  .front-art {
    position: absolute; left: 30px; top: 350px; width: 440px; height: 331px;
    background: linear-gradient(165deg, var(--cover-yellow) 25%, var(--art-pink) 60%, var(--art-teal) 85%);
  }
  .front-author {
    position: absolute; left: 0; right: 0; bottom: 0; height: 55px;
    display: flex; align-items: center; justify-content: center;
    font-family: "Libre Baskerville", serif; font-weight: 700;
    font-size: 19px; text-transform: uppercase; color: var(--ink);
  }
</style>
</head>
<body>
  <main class="cover-wrap">
    <div class="bottom-band"></div>

    <section class="back-cover">
      <header class="back-title">
        <div class="kicker">PAST SIXTY?</div>
        <div class="headline">HUNTING FOR YOUR FINAL POST?</div>
      </header>
      <div class="blurb">
        <p class="blurb-quote">'It explains how to ensure your CV gets attention.'</p>
        <ul class="blurb-points">
          <li>It gives you all the tips you need to write a killer CV.</li>
          <li>It explains how ensure that your CV gets attention.</li>
          <li>It advises you how to approach your local job agency.</li>
          <li>It guides you through the steps you need to take to make effective use of your network.</li>
        </ul>
        <p>This book, written by a top recruiter, draws upon thirty years of recruitment experience. He interviewed over a thousand candidates and developed a highly successful job application formula that you will learn in this book. This tried and tested formula helped his candidates to achieve a 70% ‘interview to offer’ rate and will help you land your next role.</p>
        <p>Whether you are a top executive, a contractor or seeking part-time work, this book will show you how to apply this job application formula and break free of a CV-based job application cycle, which is simply not effective for the over 50s.</p>
        <p>This book will help you to secure the job you want on your terms.</p>
      </div>
      <div class="back-art" role="img" aria-label="Small illustration of a figure sitting on top of a faceted mountain peak among clouds"></div>
      <div class="barcode-space"></div>
    </section>

    <section class="spine">
      <div class="spine-text">
        <span class="kicker">PAST SIXTY?</span>
        <span class="headline">&nbsp;HUNTING FOR YOUR FINAL POST?</span>
        <span class="spine-author">GARETH MILLBROOK-ASHDOWN</span>
      </div>
    </section>

    <section class="front-cover">
      <header class="front-title">
        <div class="kicker">PAST SIXTY?</div>
        <h1 class="headline">HUNTING FOR<br>YOUR FINAL<br>POST?</h1>
      </header>
      <div class="front-art" role="img" aria-label="Illustration of a job seeker with a backpack sitting on the peak of a faceted teal and pink mountain, with a thought cloud and drifting clouds"></div>
      <div class="front-author">Gareth Millbrook-Ashdown</div>
    </section>
  </main>
</body>
</html>
```